Refresh of far from plain IT company website

Our web site is starting to show it's age. You can see the existing site here: www.plumbwick.net. As a growing company we want to come across as a dynamic collection of IT experts.

We want to update the design so are open to any colour palette and look, but want to retain our current table logo. We use the logo on our business cards but with a white background - see the attached file, so you don't need to keep the brown or the green.

The design should consider the range of browsers that will be looking at the site - so please show how it will look on a wide screen laptop and a 768x1024 tablet.

We want to add some pages about our team and their skills, probably with photos of each person on the team.

This is an uncoded project - the PSD files of the design is required, not coding.
Updates

Thanks everyone for the submissions so far.  It's a holiday day in the UK today but we will get some feedback on the designs so far out to you.

Target Market(s)

Architects and other creative types looking for IT support

Industry/Entity Type

Business

Font styles to use
Serif
Sans Serif

Requirements
Must have
• Must look good on a laptop and an iPad.

```html
<!DOCTYPE html>
<html lang="en">
<head>
<meta charset="utf-8">
<title>plumbwick – IT support</title>
<link rel="stylesheet" href="https://fonts.googleapis.com/css2?family=Lato:wght@300;400;700&family=Oswald:wght@300;400&display=swap">
<style>
:root{
  --ink:#333;
  --muted:#6b6b6b;
  --magenta:#b0124f;
  --gold:#d9a400;
  --topbar:#3a3a3a;
  --footer:#3b3b3b;
  --footer-deep:#2c2c2c;
  --sage:#809d93;
  --sage-light:#9ab2a9;
  --line:#e3e3e3;
  --white:#fff;
}
*{margin:0;padding:0;box-sizing:border-box}
html,body{width:676px;height:1200px;overflow:hidden;background:#fff}
body{font-family:"Lato",sans-serif;color:var(--ink)}
.page{position:relative;width:676px;height:1200px;overflow:hidden}
.abs{position:absolute}

/* top bar */
.topbar{left:0;top:0;width:676px;height:18px;background:var(--topbar);color:#e6e6e6;font-size:8px;display:flex;justify-content:flex-end;align-items:center;gap:6px;padding-right:78px}
.topbar svg{width:9px;height:9px;fill:#e6e6e6}
.topbar span{margin-right:6px}

/* header */
.header{left:0;top:18px;width:676px;height:48px;background:var(--white)}
.brand{left:80px;top:12px;display:flex;align-items:center;gap:8px}
.brand-mark{width:14px;height:14px;background:var(--gold)}
.brand-name{font-weight:700;font-size:20px;color:var(--magenta);letter-spacing:.2px}
.nav{left:261px;top:17px;display:flex;font-size:8.5px;color:#444}
.nav a{color:inherit;text-decoration:none;padding:4px 0;margin-right:17px}
.nav a.active{background:var(--magenta);color:#fff;padding:4px 6px;border-radius:2px;margin-right:12px}

/* hero */
.hero{left:0;top:66px;width:676px;height:221px;background:linear-gradient(90deg,#2a3340 0%,#3f4b58 45%,#5a6877 70%,#3b4552 100%)}
.hero-photo{left:380px;top:0;width:296px;height:221px;background:radial-gradient(ellipse at 55% 55%,#7ea7c4 0%,#40607a 35%,#222a33 80%)}
.hero-title{left:75px;top:58px;font-family:"Oswald",sans-serif;font-weight:300;font-size:26px;line-height:32px;color:#c9cdd2}
.hero-arrows{left:74px;top:190px;display:flex;gap:4px}
.round-btn{width:20px;height:20px;border:1.2px solid #c9cdd2;border-radius:50%;display:flex;align-items:center;justify-content:center}
.round-btn svg{width:8px;height:8px;stroke:#c9cdd2;fill:none;stroke-width:1.6}

/* welcome */
.welcome-title{left:99px;top:304px;width:122px;text-align:center;font-weight:300;font-size:24px;letter-spacing:.5px;color:#222}
.welcome-sub{left:99px;top:334px;width:122px;text-align:center;font-weight:300;font-size:14px;color:#333}
.welcome-rule{left:239px;top:302px;width:1px;height:54px;background:#d9d9d9}
.welcome-text{left:256px;top:309px;width:325px;font-size:9px;line-height:13.5px;color:var(--muted);font-weight:300}
.divider{left:74px;top:372px;width:528px;height:1px;background:var(--line)}

/* services */
.services{left:74px;top:389px;display:flex;gap:5.7px}
.service{width:101px;height:91px;background:var(--sage);position:relative}
.service-icon{position:absolute;left:28px;top:11px;width:45px;height:45px;border-radius:50%;background:#fff;display:flex;align-items:center;justify-content:center}
.service-icon svg{width:22px;height:22px;fill:#333;stroke:#333}
.service-label{position:absolute;left:0;bottom:0;width:100%;height:24px;background:var(--sage-light);color:#fff;font-weight:300;font-size:13px;text-align:center;line-height:24px}

/* mission */
.mission{left:0;top:502px;width:676px;height:172px;background:linear-gradient(90deg,#e9e6e2 0%,#f6f4f1 45%,#e3ddd5 75%,#efebe6 100%)}
.mission-photo{left:440px;top:6px;width:152px;height:166px;background:linear-gradient(180deg,#b98d74 0%,#2c3138 45%,#1e2228 100%);border-radius:60px 60px 0 0}
.mission-title{left:75px;top:512px;font-weight:300;font-size:23px;color:#333}
.mission-text{left:75px;top:545px;width:345px;font-size:9px;line-height:13.5px;color:#333}
.mission-text strong{display:block;margin-top:6px;margin-bottom:6px}
.mission-text ul{padding-left:16px}
.mission-text li{margin-bottom:6px;font-size:8.5px;line-height:12px}

/* testimonials */
.section-title{width:676px;left:0;text-align:center;font-weight:300;color:#333}
.testimonials-title{top:686px;font-size:24px}
.quote-card{top:726px;width:245px;height:76px;border:1.5px solid #dedede;border-radius:3px;background:#fff}
.quote-card::after{content:"";position:absolute;left:24px;bottom:-9px;width:14px;height:14px;background:#fff;border-right:1.5px solid #dedede;border-bottom:1.5px solid #dedede;transform:skewX(40deg);clip-path:polygon(0 0,100% 0,100% 100%)}
.quote-avatar{position:absolute;left:8px;top:10px;width:48px;height:48px;border-radius:50%;border:1.5px solid #ddd;background:linear-gradient(180deg,#e8dcd2,#b8a798)}
.quote-text{position:absolute;left:66px;top:10px;width:172px;font-size:7px;line-height:11px;color:#444}
.quote-text b{font-family:Georgia,serif;font-size:13px;color:#bbb;vertical-align:-3px;margin-right:3px}
.quote-name{top:817px;font-size:7.5px;font-weight:700;color:#333}

/* team */
.team{left:0;top:846px;width:676px;height:163px;background:linear-gradient(180deg,#b8c3bf 0%,#d6dcd9 50%,#c4ccc9 100%)}
.team-title{top:860px;font-size:24px;color:#3a3a3a}
.team-row{left:107px;top:898px;display:flex;gap:9.3px}
.member{width:85px;text-align:center}
.member-photo{width:85px;height:77px;border:2.5px solid #fff;background:linear-gradient(180deg,#dde2e4 0%,#9ea7ad 60%,#5d656d 100%)}
.member-name{margin-top:6px;font-size:7.5px;color:#444}
.team-prev{left:78px;top:925px;border-color:#333}
.team-next{left:578px;top:925px;border-color:#333}
.team-prev svg,.team-next svg{stroke:#333}

/* footer */
.footer{left:0;top:1009px;width:676px;height:157px;background:var(--footer);color:#ddd}
.f-head{top:1021px;font-size:10.5px;font-weight:400;color:#eee;padding-bottom:6px;border-bottom:1px solid #555}
.f-links{top:1044px;display:grid;grid-template-columns:65px 60px;row-gap:10px;font-size:7.5px;color:#ccc}
.f-links span::before{content:"";display:inline-block;width:4px;height:4px;margin-right:6px;background:radial-gradient(circle,#aaa 35%,transparent 36%) 0 0/2px 2px}
.news{top:1045px;width:125px;font-size:7.2px;line-height:10.5px;color:#ccc}
.news h4{font-size:7.2px;font-weight:700;color:#eee;margin-bottom:2px}
.news em{color:#3d8fd1;font-size:7px}
.news p{margin-bottom:15px}
.contact{top:1047px;left:346px;font-size:7.2px;line-height:10.5px;color:#ccc}
.contact-row{display:flex;gap:9px;margin-bottom:8px}
.contact-row svg{width:9px;height:10px;fill:#999;flex:none}
.contact-row strong{font-size:8.5px;color:#eee}
.field{left:488px;width:114px;height:18px;background:#2b2b2b;font-size:6.5px;color:#bbb;padding:5px 6px}
.submit{left:489px;top:1138px;width:37px;height:14px;background:#e6e6e6;color:#333;font-size:7px;font-weight:700;text-align:center;line-height:14px}

/* bottom bar */
.bottombar{left:0;top:1166px;width:676px;height:34px;background:var(--footer-deep)}
.subscribe{left:74px;top:1176px;width:131px;height:15px;background:#3a3a3a;border:1px solid #4a4a4a;font-size:7px;color:#aaa;padding:3px 5px}
.go{left:210px;top:1176px;width:23px;height:15px;background:#ddd;color:#333;font-size:7.5px;font-weight:700;text-align:center;line-height:15px}
.social{left:304px;top:1174px;display:flex;gap:6px}
.social span{width:18px;height:18px;border-radius:50%;background:#e0e0e0}
.copyright{left:440px;top:1179px;width:162px;text-align:right;font-size:7px;color:#ddd}
</style>
</head>
<body>
<div class="page">

  <div class="abs topbar">
    <svg viewBox="0 0 10 10"><path d="M2 0.5l2 2-1 1.2c.6 1.3 1.6 2.3 2.9 2.9l1.2-1 2 2-1.3 1.8C4 9 1 6 .3 1.8z"/></svg>
    <span>020 7946 0123</span>
    <svg viewBox="0 0 10 10"><path d="M0 2h10v6H0z M0 2l5 3.5L10 2" stroke="#3a3a3a" stroke-width=".8"/></svg>
    <span>website@plumbwick.net</span>
  </div>

  <header class="abs header">
    <div class="abs brand"><span class="brand-mark"></span><span class="brand-name">plumbwick</span></div>
    <nav class="abs nav">
      <a class="active">Home</a><a>About us</a><a>What we do</a><a>News blog</a><a>Articles</a><a>Clients</a><a>Partners</a>
    </nav>
  </header>

  <section class="abs hero">
    <div class="abs hero-photo" role="img" aria-label="Businessman holding a glowing globe linked to a laptop and tablet"></div>
    <h1 class="abs hero-title">Provides a high quality,<br>one-stop IT support<br>solution for your business</h1>
    <div class="abs hero-arrows">
      <span class="round-btn"><svg viewBox="0 0 8 8"><path d="M5.5 1L2.5 4l3 3"/></svg></span>
      <span class="round-btn"><svg viewBox="0 0 8 8"><path d="M2.5 1l3 3-3 3"/></svg></span>
    </div>
  </section>

  <h2 class="abs welcome-title">WELCOME</h2>
  <div class="abs welcome-sub">plumbwick</div>
  <div class="abs welcome-rule"></div>
  <p class="abs welcome-text">Plumbwick was established with a specific aim: to consistently deliver an advanced and comprehensive IT service for ambitious growing companies across all industry sectors.</p>
  <div class="abs divider"></div>

  <div class="abs services">
    <div class="service"><div class="service-icon"><svg viewBox="0 0 22 22"><rect x="2" y="3" width="18" height="12" rx="1"/><rect x="4" y="5" width="14" height="8" fill="#fff" stroke="none"/><rect x="9" y="15" width="4" height="3"/><rect x="6" y="18" width="10" height="1.5"/></svg></div><div class="service-label">IT Support</div></div>
    <div class="service"><div class="service-icon"><svg viewBox="0 0 22 22" stroke="none"><circle cx="11" cy="6" r="3"/><circle cx="5" cy="9" r="2.5"/><circle cx="17" cy="9" r="2.5"/><path d="M6 17c0-4 2-6 5-6s5 2 5 6z"/><path d="M1 17c0-3 1.5-5 4-5 1 0 1.5.3 2 .6-1 1.2-1.5 2.6-1.5 4.4z"/><path d="M21 17c0-3-1.5-5-4-5-1 0-1.5.3-2 .6 1 1.2 1.5 2.6 1.5 4.4z"/></svg></div><div class="service-label">Consultancy</div></div>
    <div class="service"><div class="service-icon"><svg viewBox="0 0 22 22" fill="none" stroke-width="1.6"><circle cx="11" cy="4" r="1.8"/><path d="M10 6L5 19M12 6l5 13M6.5 13h9"/></svg></div><div class="service-label">CAD</div></div>
    <div class="service"><div class="service-icon"><svg viewBox="0 0 22 22" stroke-width="1"><rect x="3" y="3" width="9" height="12" fill="none"/><path d="M5 6h5M5 8.5h5M5 11h5"/><rect x="10" y="10" width="10" height="7" fill="#fff"/><path d="M13 19h4"/></svg></div><div class="service-label">Hosting</div></div>
    <div class="service"><div class="service-icon"><svg viewBox="0 0 22 22" stroke="none"><circle cx="8" cy="13" r="4.5"/><circle cx="8" cy="13" r="1.6" fill="#fff"/><circle cx="15.5" cy="6.5" r="3.2"/><circle cx="15.5" cy="6.5" r="1.1" fill="#fff"/><path d="M7 6.5h2v2H7zM2.5 12h2v2h-2zM11.5 12h2v2h-2zM7 17.5h2v2H7zM14.8 1.5h1.4v1.5h-1.4zM19 5.8h1.5v1.4H19z"/></svg></div><div class="service-label">Development</div></div>
  </div>

  <section class="abs mission">
    <div class="abs mission-photo" role="img" aria-label="Smiling businessman in a dark suit and striped tie"></div>
  </section>
  <h2 class="abs mission-title">Our Mission</h2>
  <div class="abs mission-text">
    <p>Plumbwick's mission is to be the premier IT services partner and provider of software, hardware and support solutions for progressive businesses.</p>
    <strong>To achieve this we shall:</strong>
    <ul>
      <li>Employ, encourage and empower quality members of staff who aspire to offer the highest level of service.</li>
      <li>Commit to always exceed the expectations of our customers.</li>
      <li>Commit to always exceed the expectations of our customers.</li>
    </ul>
  </div>

  <h2 class="abs section-title testimonials-title">Client Testimonials</h2>
  <div class="abs quote-card" style="left:85px">
    <div class="quote-avatar" role="img" aria-label="Portrait of a male client"></div>
    <p class="quote-text"><b>“</b>Lorem ipsum donlor ameti coinsecte adsicn elit sed do eiusmod tempor incidwiunt utboret d magna aliqua. Ut enim ad minienia quis nostru exercitation ullamco laboriisi ut aliquip ex ea com co Nemo enim ipsam voluptatem quia voluptas.</p>
  </div>
  <div class="abs quote-card" style="left:346px">
    <div class="quote-avatar" role="img" aria-label="Portrait of a female client"></div>
    <p class="quote-text"><b>“</b>Lorem ipsum donlor ameti coinsecte adsicn elit sed do eiusmod tempor incidwiunt utboret d magna aliqua. Ut enim ad minienia quis nostru exercitation ullamco laboriisi ut aliquip ex ea com co Nemo enim ipsam voluptatem quia voluptas.</p>
  </div>
  <div class="abs quote-name" style="left:85px">Mr. Client Name</div>
  <div class="abs quote-name" style="left:346px">Mrs. Client Name</div>

  <section class="abs team"></section>
  <h2 class="abs section-title team-title">Meet The Team</h2>
  <span class="abs round-btn team-prev"><svg viewBox="0 0 8 8"><path d="M5.5 1L2.5 4l3 3"/></svg></span>
  <span class="abs round-btn team-next"><svg viewBox="0 0 8 8"><path d="M2.5 1l3 3-3 3"/></svg></span>
  <div class="abs team-row">
    <div class="member"><div class="member-photo" role="img" aria-label="Team member portrait"></div><div class="member-name">Mrs. Member Name</div></div>
    <div class="member"><div class="member-photo" role="img" aria-label="Team member portrait"></div><div class="member-name">Mr. Member Name</div></div>
    <div class="member"><div class="member-photo" role="img" aria-label="Team member portrait"></div><div class="member-name">Mr. Member Name</div></div>
    <div class="member"><div class="member-photo" role="img" aria-label="Team member portrait"></div><div class="member-name">Mrs. Member Name</div></div>
    <div class="member"><div class="member-photo" role="img" aria-label="Team member portrait"></div><div class="member-name">Mrs. Member Name</div></div>
  </div>

  <footer class="abs footer"></footer>
  <h3 class="abs f-head" style="left:74px;width:111px">Quick Links</h3>
  <h3 class="abs f-head" style="left:201px;width:130px">Latest News</h3>
  <h3 class="abs f-head" style="left:346px;width:126px">Contact Information</h3>
  <h3 class="abs f-head" style="left:488px;width:114px">Quick Contact</h3>

  <div class="abs f-links" style="left:74px">
    <span>Home</span><span>Clients</span>
    <span>About us</span><span>Partners</span>
    <span>What we do</span><span>Contact</span>
    <span>News blog</span><span>Support</span>
    <span>Articles</span><span>Terms</span>
  </div>

  <div class="abs news" style="left:201px">
    <h4>Lorem ipsum dolor sit</h4>
    <p>Sed diam nonmy nibh eumod tinci ut dolore magna aliquam erat volutpat.<br><em>12/JAN/2014</em></p>
    <h4>Lorem ipsum dolor sit</h4>
    <p>Sed diam nonmy nibh eumod tinci ut dolore magna aliquam erat volutpat.<br><em>12/JAN/2014</em></p>
  </div>

  <div class="abs contact">
    <div class="contact-row"><svg viewBox="0 0 9 10"><path d="M4.5 0a3.3 3.3 0 0 1 3.3 3.3C7.8 6 4.5 10 4.5 10S1.2 6 1.2 3.3A3.3 3.3 0 0 1 4.5 0z"/><circle cx="4.5" cy="3.3" r="1.2" fill="#3b3b3b"/></svg><div>Plumbwick.net Ltd<br>Harlow House 48-52 Vale Road<br>London EC2A 4QP<br>United Kingdom</div></div>
    <div class="contact-row"><svg viewBox="0 0 9 10"><path d="M2 .5l2 2-1 1.2c.6 1.3 1.6 2.3 2.9 2.9l1.2-1 1.6 2-1.3 1.8C3.5 9 .5 6 .2 1.8z"/></svg><strong>020 7946 0123</strong></div>
    <div class="contact-row"><svg viewBox="0 0 9 10"><path d="M0 2.5h9v5.5H0z"/><path d="M0 2.5l4.5 3L9 2.5" fill="none" stroke="#3b3b3b" stroke-width=".8"/></svg><div>website@plumbwick.net</div></div>
  </div>

  <div class="abs field" style="top:1049px">Your Name</div>
  <div class="abs field" style="top:1073px">Your Email</div>
  <div class="abs field" style="top:1096px;height:35px">Your Message</div>
  <div class="abs submit">SUBMIT</div>

  <div class="abs bottombar"></div>
  <div class="abs subscribe">enter email for subcribe</div>
  <div class="abs go">GO</div>
  <div class="abs social" aria-label="Social links"><span></span><span></span><span></span><span></span></div>
  <div class="abs copyright">© 2014 plumbwick. All right reserved.</div>

</div>
</body>
</html>
```